4th Generation Family Business Needs a New Card Design!

We are a family owned 4th Generation company. We are based in the Sydney, Australia area and we are desperately in need of a more modern and classy card. We are monumental masons who design, supply & erect lasting memorials throughout cemeteries in Sydney. Our customers are normally in a period of grieving. I have attached logo files that will need to be implemented on the card. Company was established 1935. Australian Owned and Operated. Card needs to be designed to PIXO.com specification.

Target Market(s)

Our target market is based upon people that a grieving for family members that have passed away. We also deal with alot of companies that own and operate cemeteries.

Industry/Entity Type

Business

Contact Information for Business Card

Simon Harcourt, Operations Manager, 0417293086, simon@harcourtmemorials.com.au
Lewis Harcourt, Director, 0491630572, lewis@harcourtmemorials.com.au
Phone # 02 9561 3048
Website: www.harcourtmemorials.com.au
Address: Suite 17, 8 Palfrey Lane, West Carlow, Sydney NSW 2156

Font styles to use
Serif
Decorative
Script

Requirements
Must have
• Would like to see the logo nicely implemented with a modern design. Embossed lettering would be a nice additive.

```html
<!DOCTYPE html>
<html lang="en">
<head>
<meta charset="utf-8">
<title>Harcourt Memorials – Business Card</title>
<link rel="stylesheet" href="https://fonts.googleapis.com/css2?family=Cinzel:wght@400;600&family=Open+Sans:ital,wght@0,400;0,700;1,400&display=swap">
<style>
  :root {
    --backdrop: #979797;
    --card-white: #f1f1f1;
    --card-black: #1c1a1a;
    --gold: #c9a52a;
    --ink: #1e1e1e;
    --white: #eeeeee;
  }
  html, body {
    margin: 0;
    padding: 0;
    width: 1105px;
    height: 1200px;
    overflow: hidden;
    background: var(--backdrop);
  }
  .canvas {
    position: relative;
    width: 1105px;
    height: 1200px;
  }
  .card {
    position: absolute;
    left: 182px;
    width: 746px;
    height: 427px;
    display: block;
  }
  .card-front { top: 119px; }
  .card-back { top: 637px; }
  .brand-name {
    font-family: "Cinzel", serif;
    font-weight: 600;
  }
  .person-name {
    font-family: "Cinzel", serif;
    font-weight: 400;
  }
  .body-text {
    font-family: "Open Sans", sans-serif;
  }
</style>
</head>
<body>
<main class="canvas">

  <svg class="card card-front" viewBox="0 0 540 309" role="group" aria-label="Business card front">
    <rect class="card-face" width="540" height="309" fill="var(--card-white)"/>
    <path class="gold-panel" d="M345 0 Q285 150 252 309 L540 309 L540 0 Z" fill="var(--gold)"/>

    <g class="brand-lockup" fill="var(--ink)">
      <text class="brand-name" x="133" y="142" font-size="27" text-anchor="middle" letter-spacing="1">HARCOURT</text>
      <text class="brand-name" x="133" y="168" font-size="17" text-anchor="middle" letter-spacing="2">MEMORIALS</text>
    </g>

    <text class="person-name" x="32" y="262" font-size="19" fill="var(--ink)" letter-spacing="0.5">SIMON HARCOURT</text>
    <text class="body-text" x="32" y="282" font-size="13" fill="var(--gold)">Operations Manager</text>

    <g class="contact-block body-text" fill="var(--ink)" text-anchor="end" font-size="12.5">
      <text x="518" y="166">Suite 17, 8 Palfrey Lane</text>
      <text x="518" y="186">West Carlow, Sydney NSW 2156</text>
      <text x="518" y="213"><tspan font-weight="700">Phone:</tspan> 02 9561 3048</text>
      <text x="518" y="233"><tspan font-weight="700">Mobile:</tspan> 0417293086</text>
      <text x="518" y="254" font-size="12">simon@harcourtmemorials.com.au</text>
      <text x="518" y="274" font-size="12">www.harcourtmemorials.com.au</text>
    </g>
  </svg>

  <svg class="card card-back" viewBox="0 0 540 309" role="group" aria-label="Business card back">
    <rect class="card-face" width="540" height="309" fill="var(--card-black)"/>
    <g class="brand-lockup" fill="var(--white)">
      <text class="brand-name" x="270" y="196" font-size="36" text-anchor="middle" letter-spacing="1">HARCOURT</text>
      <text class="brand-name" x="270" y="228" font-size="22" text-anchor="middle" letter-spacing="3">MEMORIALS</text>
    </g>
    <text class="body-text" x="270" y="276" font-size="14" font-style="italic" fill="var(--white)" text-anchor="middle" letter-spacing="1">www.harcourtmemorials.com.au</text>
  </svg>

</main>
</body>
</html>
```